A website for a Maltese Law Firm

Our law firm needs a website to further its business. The site should have a simple yet effective design. We would need the following sections: About us, Practice Areas, About Malta, Contact. These should be further split as follows:

About us: Our firm, Our values, What others say, Offices

Practice Areas: Crimimal, Citizenship & Residence, Sovereign Patron Pathway, Criminal Defence, Civil Litigation, Arbitration and ADR, Commercial and Corporate, Media Law.

About Malta: just one section.

Contact: Just one section

We would also need a news feed at the front of the site to include latest news regarding our cases.

At the bottom we need a section for our Terms and a Privacy Statement.

Our logo is being attached.

Target Market(s)

All clients looking for legal assistance in Malta

Industry/Entity Type

Legal

Coding

Coded - Design and coding required

Number of Pages Required

1 page

Requirements
Must have
• It must be simple yet striking.

```html
<!DOCTYPE html>
<html lang="en">
<head>
<meta charset="utf-8">
<title>Mercer &amp; Halloway Advocates</title>
<link rel="stylesheet" href="https://fonts.googleapis.com/css2?family=Roboto:wght@300;400;500;700&family=Open+Sans:wght@400;600&family=Oswald:wght@600&display=swap">
<style>
:root{
  --navy:#2b3243;
  --slate:#3c4559;
  --beige:#e9dfd5;
  --beige-light:#f1ece6;
  --paper:#ffffff;
  --mist:#ececec;
  --ink:#3a3f4a;
  --accent:#a9bde6;
  --footer:#262b36;
  --icon-light:#d8dbe2;
}
*{box-sizing:border-box;margin:0;padding:0}
html,body{width:685px;height:1200px;overflow:hidden}
body{font-family:"Open Sans",Arial,sans-serif;color:var(--ink);background:var(--paper)}
.page{position:relative;width:685px;height:1200px;overflow:hidden}
.abs{position:absolute}

/* header */
.site-header{position:absolute;left:0;top:0;width:685px;height:71px;background:var(--beige)}
.header-shape{position:absolute;left:0;top:0}
.brand{position:absolute;left:56px;top:30px;font-family:"Roboto",sans-serif;font-weight:500;color:#fff;font-size:10.5px;letter-spacing:.4px;white-space:nowrap}
.call{position:absolute;left:381px;top:7px;font-family:"Roboto",sans-serif;font-size:7.5px;color:var(--icon-light)}
.call b{color:#fff;font-weight:500}
.top-icons{position:absolute;left:515px;top:5px;display:flex;gap:3px}
.icon-box{width:13px;height:13px;border:1px solid #8a91a1;display:flex;align-items:center;justify-content:center}
.nav-band{position:absolute;left:200px;top:42px;width:485px;height:29px;background:var(--beige-light)}
.main-nav{position:absolute;top:54px;font-family:"Roboto",sans-serif;font-size:7.5px;color:var(--navy);text-transform:uppercase}
.nav-slash{position:absolute;top:48px;width:1px;height:16px;background:#d3c9bf;transform:skewX(-25deg)}
.nav-active{position:absolute;left:297px;top:65px;width:0;height:0;border-left:6px solid transparent;border-bottom:5px solid var(--navy)}

/* hero */
.hero{position:absolute;left:0;top:71px;width:685px;height:303px;background:linear-gradient(90deg,#8c6f55 0%,#5e5550 30%,#3f4758 55%,#6b5a4b 80%,#8d7462 100%)}
.hero-lede{position:absolute;left:57px;top:208px;font-family:"Roboto",sans-serif;font-weight:300;font-size:14px;line-height:19px;color:#fff}
.hero-title{position:absolute;left:56px;top:252px;font-family:"Oswald",sans-serif;font-weight:600;font-size:28.5px;color:#fff;white-space:nowrap}
.contact-card{position:absolute;left:461px;top:55px;width:168px;height:193px;background:rgba(70,78,96,.82);border:1px solid rgba(255,255,255,.35);border-radius:3px}
.contact-card-head{position:absolute;left:0;top:0}
.contact-card-title{position:absolute;left:0;top:13px;width:168px;text-align:center;font-family:"Roboto",sans-serif;font-size:9px;font-weight:500;color:#fff}
.field{position:absolute;left:13px;width:141px;height:19px;background:#e9eaed;border:1px solid #c9ccd3;font-family:"Roboto",sans-serif;font-size:6.5px;color:#555b66;padding:5px 5px}
.submit{position:absolute;left:52px;top:160px;width:63px;height:22px;background:var(--navy);color:#fff;font-family:"Roboto",sans-serif;font-size:6.5px;font-weight:700;text-align:center;line-height:22px}
.hero-arrows{position:absolute;left:579px;top:271px}

/* welcome */
.welcome-title{position:absolute;left:56px;top:394px;font-family:"Roboto",sans-serif;font-weight:300;font-size:20px;line-height:24px;color:var(--navy)}
.welcome-text{position:absolute;left:56px;top:425px;width:304px;font-size:6.2px;line-height:11.7px;color:#6d7280}
.welcome-text p+p{margin-top:11px}
.btn-dark{position:absolute;background:var(--slate);color:#fff;font-family:"Roboto",sans-serif;font-weight:500;font-size:7px;text-align:center;border-radius:2px}
.welcome-photo{position:absolute;left:371px;top:402px;width:258px;height:158px;border:3px solid #fff;box-shadow:0 0 0 1px #ddd;background:linear-gradient(120deg,#5a3a22 0%,#2f3442 40%,#b7b4ad 75%,#e2ddd4 100%)}

/* practice */
.practice{position:absolute;left:0;top:592px;width:685px;height:167px;background:var(--slate)}
.practice-title{position:absolute;left:0;top:19px;width:685px;text-align:center;font-family:"Roboto",sans-serif;font-weight:400;font-size:19px;color:#fff}
.area{position:absolute;top:64px;width:175px;color:#fff}
.area-head{display:flex;align-items:center;gap:6px;font-family:"Roboto",sans-serif;font-size:9.5px;font-weight:500;letter-spacing:.2px;white-space:nowrap}
.area-text{margin-top:8px;width:160px;font-size:6.3px;line-height:10.8px;color:#e4e7ec}
.area-go{position:absolute;top:130px}
.area-divider{position:absolute;top:64px;width:1px;height:74px;background:#7a8396}

/* testimonial */
.testimonial{position:absolute;left:0;top:759px;width:685px;height:158px;background:#fff}
.testimonial-shade{position:absolute;left:120px;top:0;width:445px;height:14px;background:radial-gradient(ellipse at top,rgba(0,0,0,.12),rgba(0,0,0,0) 70%)}
.avatar-ring{position:absolute;left:55px;top:27px}
.avatar-photo{position:absolute;left:67px;top:40px;width:86px;height:86px;border-radius:50%;background:radial-gradient(circle at 50% 40%,#d9d6d2 0%,#9aa0aa 55%,#3a3f4c 100%)}
.quote-name{position:absolute;left:357px;top:35px;font-family:"Roboto",sans-serif;font-size:8.5px;font-weight:500;color:var(--navy)}
.quote-bars{position:absolute;left:330px;top:39px}
.quote-text{position:absolute;left:190px;top:56px;width:436px;text-align:center;font-size:6.3px;line-height:11.8px;color:#555b66;font-weight:600}
.quote-dots{position:absolute;left:347px;top:118px;display:flex;gap:5px}
.quote-dots span{width:26px;height:2px;background:#5d6270}
.quote-dots span.on{background:var(--accent)}

/* info */
.info{position:absolute;left:0;top:917px;width:685px;height:192px;background:var(--mist)}
.info-title{position:absolute;top:25px;font-family:"Roboto",sans-serif;font-weight:500;font-size:14px;color:#3a3f4a;text-transform:uppercase}
.story-text{position:absolute;left:56px;top:48px;width:172px;font-size:6.2px;line-height:11.7px;color:#8a8e97}
.news-item{position:absolute;left:258px;display:flex;gap:8px}
.news-date{width:27px;height:27px;background:var(--slate);color:#fff;border-radius:3px;font-family:"Roboto",sans-serif;font-weight:500;font-size:11px;display:flex;align-items:center;justify-content:center}
.news-date.dark{background:#1d212b}
.news-head{font-size:6.6px;color:#3a3f4a;margin-top:2px}
.news-sub{font-size:6px;color:#8a8e97;margin-top:3px}
.contact-lines{position:absolute;left:465px;top:59px;font-family:"Roboto",sans-serif;font-size:6.8px;line-height:14.6px;color:#3a3f4a}
.contact-lines b{font-weight:500}
.subscribe{position:absolute;left:465px;top:144px;width:163px;height:22px;background:#f7f7f7;border:1px solid #d6d6d6;font-size:6px;color:#a0a4ab;padding:7px 8px}
.subscribe-go{position:absolute;left:603px;top:144px;width:26px;height:22px;background:var(--slate);color:#fff;font-family:"Roboto",sans-serif;font-weight:700;font-size:7.5px;text-align:center;line-height:22px}

/* footer */
.footer-nav{position:absolute;left:0;top:1109px;width:685px;height:33px;background:var(--beige)}
.footer-links{position:absolute;left:56px;top:12px;font-family:"Roboto",sans-serif;font-size:7px;color:#fff;word-spacing:1px}
.footer-links i{font-style:normal;margin:0 6px}
.footer-icons{position:absolute;left:513px;top:7px;display:flex;gap:4px}
.footer-icons .icon-box{width:20px;height:20px;border-color:#9da3af;background:#f4f1ed}
.legal{position:absolute;left:0;top:1142px;width:685px;height:58px;background:var(--footer);text-align:center;color:#fff}
.legal-copy{margin-top:8px;font-size:6.8px}
.legal-note{margin-top:8px;font-size:6px;line-height:10px;color:#c9ccd3}
</style>
</head>
<body>
<div class="page">

  <header class="site-header">
    <svg class="header-shape" width="685" height="71" viewBox="0 0 685 71" aria-hidden="true">
      <polygon points="0,0 234,0 200,71 0,71" fill="#2b3243"/>
      <polygon points="358,0 628,0 612,24 366,24" fill="#2b3243"/>
    </svg>
    <div class="brand">Mercer &amp; Halloway Advocates</div>
    <div class="call">Call Today: <b>+1.555 010 2040</b></div>
    <div class="top-icons" aria-label="Share links">
      <span class="icon-box"><svg width="8" height="8" viewBox="0 0 8 8"><circle cx="6.3" cy="1.5" r="1.3" fill="#d8dbe2"/><circle cx="1.7" cy="4" r="1.3" fill="#d8dbe2"/><circle cx="6.3" cy="6.5" r="1.3" fill="#d8dbe2"/><path d="M6.3 1.5 1.7 4l4.6 2.5" fill="none" stroke="#d8dbe2" stroke-width=".8"/></svg></span>
      <span class="icon-box"><svg width="8" height="7" viewBox="0 0 8 7"><path d="M.5 .5h7v4.2H3.2L1.4 6.5V4.7H.5z" fill="#d8dbe2"/></svg></span>
      <span class="icon-box"><svg width="8" height="6" viewBox="0 0 8 6"><rect x=".5" y=".5" width="7" height="5" fill="none" stroke="#d8dbe2"/><path d="M.5 .5 4 3.5 7.5 .5" fill="none" stroke="#d8dbe2"/></svg></span>
      <span class="icon-box"><svg width="8" height="7" viewBox="0 0 8 7"><rect x="2" y="0" width="4" height="2" fill="#d8dbe2"/><rect x="0" y="2.5" width="8" height="3" fill="#d8dbe2"/><rect x="2" y="5" width="4" height="2" fill="#d8dbe2"/></svg></span>
      <span class="icon-box"><svg width="7" height="7" viewBox="0 0 7 7"><path d="M3.5 0v7M0 3.5h7" stroke="#d8dbe2" stroke-width="1.4"/></svg></span>
    </div>
    <div class="nav-band"></div>
    <nav>
      <span class="main-nav" style="left:267px">About</span>
      <span class="nav-slash" style="left:316px"></span>
      <span class="main-nav" style="left:328px">Contact</span>
      <span class="nav-slash" style="left:385px"></span>
      <span class="main-nav" style="left:398px">Blog</span>
      <span class="nav-slash" style="left:436px"></span>
      <span class="main-nav" style="left:453px">FAQ's</span>
      <span class="nav-slash" style="left:490px"></span>
      <span class="main-nav" style="left:510px">Testimonials</span>
      <span class="nav-slash" style="left:578px"></span>
      <span class="main-nav" style="left:598px">Gallery</span>
    </nav>
    <span class="nav-active"></span>
  </header>

  <section class="hero" role="img" aria-label="Photo of a senior lawyer standing with two colleagues in an office">
    <p class="hero-lede">Throughout 30 years of practice, my focus<br>has been and will always be to</p>
    <h1 class="hero-title">PROTECT YOUR RIGHTS</h1>
    <form class="contact-card">
      <svg class="contact-card-head" width="168" height="48" viewBox="0 0 168 48" aria-hidden="true">
        <polygon points="0,0 168,0 168,36 96,36 84,46 72,36 0,36" fill="#2b3243"/>
      </svg>
      <div class="contact-card-title">OUR CONTACT US</div>
      <div class="field" style="top:54px">Name:*</div>
      <div class="field" style="top:78px">Phone:*</div>
      <div class="field" style="top:103px">Email:*</div>
      <div class="field" style="top:128px">Requested Appointment Time:</div>
      <div class="submit">SUBMIT</div>
    </form>
    <svg class="hero-arrows" width="52" height="20" viewBox="0 0 52 20" aria-hidden="true">
      <circle cx="10" cy="10" r="8.5" fill="none" stroke="#fff" stroke-width="1.6"/>
      <path d="M12 6 8 10 12 14" fill="none" stroke="#fff" stroke-width="1.6"/>
      <circle cx="40" cy="10" r="8.5" fill="none" stroke="#fff" stroke-width="1.6"/>
      <path d="M38 6 42 10 38 14" fill="none" stroke="#fff" stroke-width="1.6"/>
    </svg>
  </section>

  <section class="welcome">
    <h2 class="welcome-title">Welcome!</h2>
    <div class="welcome-text">
      <p>Edward P. Harlow is a 1972 graduate of the Harbor Maritime Academy in Eastport, Vermont. After a five year stint in the Navy Mr. Harlow attended Northfield College Law school where he graduated in 1980.</p>
      <p>He relocated to Brookhaven, Oregon and joined the growing law firm of Prescott and Vale, where he practiced law for the first few years of his career. Upon leaving PV Mr. Harlow began his own practice and since that time his practice has focused on Civil Litigation. His practice involves a multitude of areas including personal injury, construction and general commercial litigation. He has been lead counsel in numerous state and federal court trials both jury trials and trials to the court.</p>
    </div>
    <a class="btn-dark" style="left:56px;top:543px;width:65px;height:25px;line-height:25px">READ MORE</a>
    <div class="welcome-photo" role="img" aria-label="Photo of a lawyer in a suit signing a document at a desk"></div>
  </section>

  <section class="practice">
    <h2 class="practice-title">Our Practice Areas</h2>
    <div class="area" style="left:56px">
      <div class="area-head"><svg width="28" height="22" viewBox="0 0 28 22" aria-hidden="true"><path d="M14 1v19M6 4h16M4 20h20" stroke="#fff" stroke-width="1.6" fill="none"/><path d="M6 4 2 13h8zM22 4l-4 9h8z" stroke="#fff" stroke-width="1.2" fill="none"/><path d="M2 13a4 3 0 0 0 8 0M18 13a4 3 0 0 0 8 0" fill="#fff"/></svg>CITIZENSHIP &amp; RESIDENCE</div>
      <p class="area-text">"Search engine optimisation (SEO) is the practice of manipulating aspects of a Web site to improve its ranking in search engines.</p>
    </div>
    <div class="area-divider" style="left:238px"></div>
    <div class="area" style="left:264px">
      <div class="area-head"><svg width="28" height="22" viewBox="0 0 28 22" aria-hidden="true"><path d="M14 1v19M6 4h16M4 20h20" stroke="#fff" stroke-width="1.6" fill="none"/><path d="M6 4 2 13h8zM22 4l-4 9h8z" stroke="#fff" stroke-width="1.2" fill="none"/><path d="M2 13a4 3 0 0 0 8 0M18 13a4 3 0 0 0 8 0" fill="#fff"/></svg>CRIMINAL DEFENCE</div>
      <p class="area-text">"Search engine optimisation (SEO) is the practice of manipulating aspects of a Web site to improve its ranking in search engines.</p>
    </div>
    <div class="area-divider" style="left:445px"></div>
    <div class="area" style="left:472px">
      <div class="area-head"><svg width="28" height="22" viewBox="0 0 28 22" aria-hidden="true"><path d="M14 1v19M6 4h16M4 20h20" stroke="#fff" stroke-width="1.6" fill="none"/><path d="M6 4 2 13h8zM22 4l-4 9h8z" stroke="#fff" stroke-width="1.2" fill="none"/><path d="M2 13a4 3 0 0 0 8 0M18 13a4 3 0 0 0 8 0" fill="#fff"/></svg>CIVIL LITIGATION</div>
      <p class="area-text">"Search engine optimisation (SEO) is the practice of manipulating aspects of a Web site to improve its ranking in search engines.</p>
    </div>
    <svg class="area-go" style="left:197px" width="12" height="12" viewBox="0 0 12 12" aria-hidden="true"><circle cx="6" cy="6" r="5.3" fill="none" stroke="#fff"/><path d="M3.5 8.5 6 3l2.5 5.5L6 7z" fill="#fff"/></svg>
    <svg class="area-go" style="left:405px" width="12" height="12" viewBox="0 0 12 12" aria-hidden="true"><circle cx="6" cy="6" r="5.3" fill="none" stroke="#fff"/><path d="M3.5 8.5 6 3l2.5 5.5L6 7z" fill="#fff"/></svg>
    <svg class="area-go" style="left:612px" width="12" height="12" viewBox="0 0 12 12" aria-hidden="true"><circle cx="6" cy="6" r="5.3" fill="none" stroke="#fff"/><path d="M3.5 8.5 6 3l2.5 5.5L6 7z" fill="#fff"/></svg>
  </section>

  <section class="testimonial">
    <div class="testimonial-shade"></div>
    <svg class="avatar-ring" width="125" height="106" viewBox="0 0 125 106" aria-hidden="true">
      <path d="M108 66 123 76 103 78" fill="#a9bde6"/>
      <circle cx="61" cy="52" r="52" fill="#a9bde6"/>
      <circle cx="61" cy="52" r="46" fill="#fff"/>
    </svg>
    <div class="avatar-photo" role="img" aria-label="Portrait photo of the client giving the testimonial"></div>
    <svg class="quote-bars" width="22" height="4" viewBox="0 0 22 4" aria-hidden="true"><rect width="10" height="4" fill="#a9bde6"/><rect x="12" width="10" height="4" fill="#5d6270"/></svg>
    <div class="quote-name">DANIEL OKORO</div>
    <p class="quote-text">Lorem Ipsum is not simply random text. It has roots in a piece of classical Latin literature from 45 BC, making it over 2000 years old. Thomas Reyne, a Latin professor at Ashford Hill College in Virginia, looked up one of the more obscure Latin words, consectetur, from a Lorem Ipsum passage, and going through the cites of the word in classical literature, discovered source. Lorem Ipsum comes from sections 1.10.32 and 1.10.33 of "de Finibus.</p>
    <div class="quote-dots"><span></span><span class="on"></span><span></span></div>
  </section>

  <section class="info">
    <h3 class="info-title" style="left:56px">Success&nbsp; Story</h3>
    <p class="story-text">There are many variations of passages of Lorem Ipsum available, but the majority have suffered alteration in some form, by injected humour, or randomised words which don't look even slightly believable. If you are going to use a passage of Lorem Ipsum, you need to be sure there isn't anything embarrassing hidden in the middle of text. All the Lorem Ipsum generators.</p>
    <a class="btn-dark" style="left:57px;top:143px;width:69px;height:25px;line-height:25px;border-radius:3px">READ MORE</a>

    <h3 class="info-title" style="left:258px">News &amp; Event</h3>
    <div class="news-item" style="top:58px"><div class="news-date">06</div><div><p class="news-head">There are many variations of passages of</p><p class="news-sub">Lorem Ipsum available, but the majority have</p></div></div>
    <div class="news-item" style="top:100px"><div class="news-date">07</div><div><p class="news-head">There are many variations of passages of</p><p class="news-sub">Lorem Ipsum available, but the majority have</p></div></div>
    <div class="news-item" style="top:141px"><div class="news-date dark">08</div><div><p class="news-head">There are many variations of passages of</p><p class="news-sub">Lorem Ipsum available, but the majority have</p></div></div>

    <h3 class="info-title" style="left:465px">Contact Us</h3>
    <div class="contact-lines">
      <b>mhadvocates Law</b><br>
      <b>12/4, Harbour Lane, Valletta</b><br>
      Phone : (356) 2100 0480<br>
      Fax : (356) 2100 0481<br>
      Email : mhadvocates.example
    </div>
    <div class="subscribe">Your Email:</div>
    <div class="subscribe-go">GO!</div>
  </section>

  <footer>
    <div class="footer-nav">
      <svg class="abs" style="left:0;top:0" width="450" height="33" viewBox="0 0 450 33" aria-hidden="true"><polygon points="0,0 450,0 425,33 0,33" fill="#3c4559"/></svg>
      <div class="footer-links">ABOUT<i>/</i>CONTACT<i>/</i>BLOG<i>/</i>FAQ'S<i>/</i>TESTIMONIALS<i>/</i>GALLERY</div>
      <div class="footer-icons" aria-label="Share links">
        <span class="icon-box"><svg width="10" height="10" viewBox="0 0 8 8"><circle cx="6.3" cy="1.5" r="1.3" fill="#3c4559"/><circle cx="1.7" cy="4" r="1.3" fill="#3c4559"/><circle cx="6.3" cy="6.5" r="1.3" fill="#3c4559"/><path d="M6.3 1.5 1.7 4l4.6 2.5" fill="none" stroke="#3c4559" stroke-width=".8"/></svg></span>
        <span class="icon-box"><svg width="10" height="9" viewBox="0 0 8 7"><path d="M.5 .5h7v4.2H3.2L1.4 6.5V4.7H.5z" fill="#3c4559"/></svg></span>
        <span class="icon-box"><svg width="10" height="8" viewBox="0 0 10 8"><rect x=".5" y=".5" width="9" height="7" fill="#3c4559"/><path d="M.5 .5 5 4.5 9.5 .5" fill="none" stroke="#f4f1ed"/></svg></span>
        <span class="icon-box"><svg width="10" height="9" viewBox="0 0 10 9"><rect x="2.5" y="0" width="5" height="2.5" fill="#3c4559"/><rect x="0" y="3" width="10" height="4" fill="#3c4559"/><rect x="2.5" y="6" width="5" height="3" fill="#3c4559" stroke="#f4f1ed" stroke-width=".6"/></svg></span>
        <span class="icon-box"><svg width="9" height="9" viewBox="0 0 9 9"><path d="M4.5 0v9M0 4.5h9" stroke="#3c4559" stroke-width="2"/></svg></span>
      </div>
    </div>
    <div class="legal">
      <p class="legal-copy">Copyright © 2016 &nbsp;mhadvocates.example . All Rights Reserved.</p>
      <p class="legal-note">A Links To Other Web Sites clause informs users that you are not responsible for any third party web sites that you link to from your website,<br>and that users are responsible for reading these third parties' own Terms and Conditions or Privacy Policies.</p>
    </div>
  </footer>

</div>
</body>
</html>
```